Design a calming beauty medical salon & spa website based in Hong Kong

We need help building an informational website for a beauty salon in Hong Kong. The local salon provides facials, massages, body and other slimming treatments in a relaxing environment. We offer some non-invasive medical treatments, such as botox. Having built the business on word of mouth, it is now time for us to launch a website to help market the business better. Website requirements:

-Must be responsive
-Use vibrant but clean colours. not too many, 1-2 colours
-Must be bilingual (switch between Chinese traditional and English)
-Our current website is host on a server, not using any particular platforms like wordpress

Pages:
1/ Homepage
2/ About us (incorporate gallery of salon photos and history of company)
3/ Promotions and latest deals (and leads them to sign up for more info, maybe pop-up small window when you click on a promotion)
4/ Treatment menus
4.1/Body treatments
4.2/ Face treatments
4.3/ Slimming treatments
5/ Showcasing products sold (no e-commerce functionality, just showing off products)
6/ Contact us (tel, address, map, opening hrs)

Footer - must haves include contact us info, privacy policy, terms & conditions, copyright blurb, join our company/employment page (with a form)

For information (comparable websites we like):
http://veltora.com/
http://pambrix.com.hk/tc/aboutpambrix/background.php#centerenvi
Attaching a very first draft concept for this website
Attaching pictures of the beauty salon
Attaching logo

Target Market(s)

Hong Kong based, Chinese, females, 30-50+ age. 90% female clients.

Industry/Entity Type

Beauty Salon

Number of Pages Required

5+ page

Font styles to use
Sans Serif

Colors
f9d9e8
fbd3d4
fee3d5
fbe7d2
fee18a
fbf289
ffffff

Requirements
Must have
• interactive elements on website, such as scrolling banner photo headers
• incorporate photos of website salon
• connect to facebook page

```html
<!DOCTYPE html>
<html lang="en">
<head>
<meta charset="utf-8">
<title>Lumera Beauty</title>
<link href="https://fonts.googleapis.com/css2?family=Dancing+Script:wght@600&family=Open+Sans:wght@400;600&family=Poppins:wght@400;500&display=swap" rel="stylesheet">
<style>
:root{
  --purple:#6d1a7e;
  --purple-deep:#5c1672;
  --violet:#9b1fc4;
  --ink:#1d1d1d;
  --text:#333;
  --white:#fff;
  --map-sea:#8fb4d6;
  --map-land:#e8e6df;
}
*{margin:0;padding:0;box-sizing:border-box}
html,body{width:1200px;height:2206px;overflow:hidden;background:var(--white)}
body{position:relative;font-family:"Open Sans",Arial,sans-serif;color:var(--text)}
.abs{position:absolute}

/* header */
.site-header{position:absolute;left:0;top:0;width:1200px;height:122px;background:var(--white);box-shadow:0 2px 3px rgba(0,0,0,.12);z-index:5}
.brand{position:absolute;left:100px;top:34px;display:flex;align-items:center;gap:12px}
.brand-dot{width:44px;height:44px;border-radius:50%;background:var(--purple)}
.brand-name{font-family:"Poppins",sans-serif;font-weight:500;font-size:30px;color:var(--purple)}
.contact-line{position:absolute;left:660px;top:26px;display:flex;align-items:center;font-family:"Poppins",sans-serif;font-size:16px;color:var(--ink);gap:6px}
.social{width:34px;height:34px;border-radius:6px;background:#3b5998;margin-left:10px}
.social.alt{background:#3cae3c;margin-left:6px}
.lang{position:absolute;left:992px;top:26px;font-family:"Poppins",sans-serif;font-size:15px;color:var(--ink)}
.lang b{font-weight:400;color:var(--purple)}
.main-nav{position:absolute;left:397px;top:72px;display:flex;gap:20px;font-family:"Poppins",sans-serif;font-size:15px;color:var(--ink)}
.main-nav .active{color:var(--purple)}

/* hero */
.hero{position:absolute;left:0;top:122px;width:1200px;height:560px;background:radial-gradient(ellipse at 70% 40%,#f1d7c8 0%,#e9c3ad 22%,#c9e09d 45%,#a7d071 75%,#8fc35a 100%)}
.hero-title{position:absolute;left:100px;top:130px;font-family:"Dancing Script",cursive;font-size:72px;color:#111}
.hero-sub{position:absolute;left:100px;top:228px;font-family:"Poppins",sans-serif;font-weight:500;font-size:22px;line-height:31px;color:#111}
.btn-learn{position:absolute;left:102px;top:320px;width:132px;height:42px;border-radius:4px;background:var(--purple);color:var(--white);font-family:"Poppins",sans-serif;font-weight:500;font-size:15px;display:flex;align-items:center;justify-content:center}
.hero-arrow{position:absolute;top:200px}
.hero-wave{position:absolute;left:0;top:0}

/* services */
.section-title{font-family:"Dancing Script",cursive;font-size:40px;color:#111}
.services-title{left:128px;top:700px}
.services-intro{left:130px;top:772px;width:940px;font-family:"Poppins",sans-serif;font-size:14.5px;line-height:26px;color:#222}
.service{position:absolute;top:904px;width:258px}
.service-photo{width:258px;height:170px;border:1px solid #ddd}
.service h3{margin-top:20px;font-family:"Poppins",sans-serif;font-weight:500;font-size:21px;color:var(--purple)}
.service p{margin-top:8px;font-family:"Poppins",sans-serif;font-size:11.5px;line-height:22px;color:#333}

/* map + contact */
.map{position:absolute;left:0;top:1286px;width:1200px;height:620px;background:linear-gradient(120deg,var(--map-land) 0%,var(--map-land) 35%,var(--map-sea) 55%,#9ebedb 75%,var(--map-land) 100%)}
.contact-card{position:absolute;left:118px;top:1350px;width:374px;height:462px;background:var(--white);box-shadow:0 0 4px rgba(0,0,0,.2);z-index:3}
.contact-card .section-title{position:absolute;left:94px;top:50px}
.contact-row{position:absolute;left:72px;font-size:16.5px;line-height:24px;color:#111}
.contact-icon{position:absolute;left:-50px;top:2px}

/* footer */
.site-footer{position:absolute;left:0;top:1780px;width:1200px;height:426px}
.footer-bg{position:absolute;left:0;top:0}
.footer-brand{position:absolute;left:100px;top:200px;display:flex;align-items:center;gap:12px}
.footer-brand .brand-dot{background:var(--white)}
.footer-brand .brand-name{color:var(--white)}
.f-head{position:absolute;font-size:19px;color:var(--white)}
.f-list{position:absolute;list-style:none;font-size:13px;color:var(--white)}
.f-list.treat li{line-height:27px}
.f-list.quick li{line-height:24px}
.join-field{position:absolute;left:832px;width:256px;height:32px;border:1px solid var(--white);color:var(--white);font-size:13px;padding:6px 8px}
.btn-submit{position:absolute;left:980px;top:2040px;width:108px;height:36px;border:2px solid var(--white);border-radius:6px;color:var(--white);font-size:16px;font-weight:600;display:flex;align-items:center;justify-content:center}
.footer-rule{position:absolute;left:100px;top:2124px;width:1000px;height:1px;background:rgba(255,255,255,.6)}
.legal{position:absolute;left:104px;top:2156px;display:flex;align-items:center;gap:8px;font-size:13px;color:var(--white)}
.legal .sq{width:22px;height:22px;background:#3b5998}
.copyright{position:absolute;left:742px;top:2159px;font-size:13px;color:var(--white)}
</style>
</head>
<body>

<header class="site-header">
  <div class="brand"><span class="brand-dot"></span><span class="brand-name">Lumera Beauty</span></div>
  <div class="contact-line">
    <svg width="14" height="14" viewBox="0 0 24 24"><path fill="#4b1760" d="M6.6 10.8a15 15 0 006.6 6.6l2.2-2.2c.3-.3.7-.4 1-.2 1.1.4 2.3.6 3.6.6.6 0 1 .4 1 1V20c0 .6-.4 1-1 1A17 17 0 013 4c0-.6.4-1 1-1h3.5c.6 0 1 .4 1 1 0 1.3.2 2.5.6 3.6.1.3 0 .7-.2 1z"/></svg>
    <span>23184762</span><span>|</span>
    <svg width="14" height="16" viewBox="0 0 14 20"><rect x="1" y="1" width="12" height="18" rx="2" fill="none" stroke="#4b1760" stroke-width="2"/><circle cx="7" cy="16" r="1.2" fill="#4b1760"/></svg>
    <span>61539027</span>
    <span class="social" aria-hidden="true"></span><span class="social alt" aria-hidden="true"></span>
  </div>
  <div class="lang"><b>English</b> &nbsp;| 中文</div>
  <nav class="main-nav">
    <span class="active">Home</span><span>About us</span><span>Promotions &amp; Latest deals</span>
    <span>Treatment ▾</span><span>Products Showcase</span><span>Contact us</span>
  </nav>
</header>

<section class="hero" role="img" aria-label="Banner photo of a woman with glowing skin touching her face on a soft green background">
  <div class="hero-title">Lumera Beauty</div>
  <div class="hero-sub">Contrary To Popular Belief, Lorem<br>Ipsum Contrary Is Not Simply Random</div>
  <div class="btn-learn">LEARN MORE</div>
  <svg class="hero-arrow" style="left:36px" width="34" height="54" viewBox="0 0 34 54"><path d="M28 4L6 27l22 23" fill="none" stroke="#333" stroke-width="6"/></svg>
  <svg class="hero-arrow" style="left:1128px" width="34" height="54" viewBox="0 0 34 54"><path d="M6 4l22 23L6 50" fill="none" stroke="#333" stroke-width="6"/></svg>
  <svg class="hero-wave" width="1200" height="560" viewBox="0 0 1200 560">
    <defs><linearGradient id="heroLine" x1="0" x2="1"><stop offset="0" stop-color="#6d1a7e"/><stop offset="1" stop-color="#b860d6"/></linearGradient></defs>
    <path d="M0 498C120 470 240 452 360 458C560 470 700 540 900 556C1040 566 1120 560 1200 548V560H0Z" fill="#fff"/>
    <path d="M0 498C120 470 240 452 360 458C560 470 700 540 900 556C1040 566 1120 560 1200 548" fill="none" stroke="url(#heroLine)" stroke-width="6"/>
  </svg>
</section>

<h2 class="abs section-title services-title">Our Beauty Services</h2>
<p class="abs services-intro">To take care of all aspects of the skin different needs, providing facial and body care. Customers can enjoy a more efficient and beautiful skin treatment in a relaxed and comfortable environment. Together with noble Swiss brand Lumera organic material series for home care, In order to push the quality of skin to the pinnacle.</p>

<article class="service" style="left:130px">
  <div class="service-photo" role="img" aria-label="Photo of a facial mask treatment" style="background:linear-gradient(135deg,#e6d2bf,#8d6f5c 60%,#c9ad94)"></div>
  <h3>Facials</h3>
  <p>There are many variations of passages of Lorem Ipsum available, the majority have suffered alteration.</p>
</article>
<article class="service" style="left:475px">
  <div class="service-photo" role="img" aria-label="Photo of a relaxing hot stone body treatment" style="background:linear-gradient(160deg,#d9d6d3,#b89e8c 55%,#f1efed)"></div>
  <h3>Body Care</h3>
  <p>There are many variations of passages of Lorem Ipsum available, the majority have suffered alteration.</p>
</article>
<article class="service" style="left:820px">
  <div class="service-photo" role="img" aria-label="Photo of a slim waist with a measuring tape" style="background:linear-gradient(90deg,#ecebea,#e0c2ae 50%,#eeeceb)"></div>
  <h3>Thin Shape</h3>
  <p>There are many variations of passages of Lorem Ipsum available, the majority have suffered alteration.</p>
</article>

<div class="map" role="img" aria-label="Street map of Tsim Sha Tsui and the harbour showing the salon location"></div>

<aside class="contact-card">
  <h2 class="section-title">Contact Us</h2>
  <div class="contact-row" style="top:134px">
    <svg class="contact-icon" width="20" height="28" viewBox="0 0 20 28"><path d="M10 0a10 10 0 00-10 10c0 7.5 10 18 10 18s10-10.5 10-18A10 10 0 0010 0z" fill="#6d1a7e"/><circle cx="10" cy="10" r="3.5" fill="#fff"/></svg>
    12th Floor, Silver Lotus Centre,<br>21-23 Hanoi Road,<br>Tsim Sha Tsui, Kowloon</div>
  <div class="contact-row" style="top:216px">
    <svg class="contact-icon" width="24" height="24" viewBox="0 0 24 24"><path fill="#6d1a7e" d="M6.6 10.8a15 15 0 006.6 6.6l2.2-2.2c.3-.3.7-.4 1-.2 1.1.4 2.3.6 3.6.6.6 0 1 .4 1 1V20c0 .6-.4 1-1 1A17 17 0 013 4c0-.6.4-1 1-1h3.5c.6 0 1 .4 1 1 0 1.3.2 2.5.6 3.6.1.3 0 .7-.2 1z"/></svg>
    23184762 &nbsp;| &nbsp;61539027</div>
  <div class="contact-row" style="top:276px">
    <svg class="contact-icon" width="28" height="22" viewBox="0 0 28 22"><rect width="28" height="22" rx="2" fill="#6d1a7e"/><path d="M2 3l12 9 12-9" fill="none" stroke="#fff" stroke-width="2"/></svg>
    hello@lumerabeauty.com.hk</div>
  <div class="contact-row" style="top:348px">
    <svg class="contact-icon" width="26" height="26" viewBox="0 0 26 26" style="top:6px"><circle cx="13" cy="13" r="11" fill="none" stroke="#6d1a7e" stroke-width="3"/><path d="M13 7v7h5" fill="none" stroke="#6d1a7e" stroke-width="3"/></svg>
    Mon - Fri : 10:30 am to 9:30 pm<br>Sat &amp; Holidays: 10:30 am to 7:30 pm</div>
</aside>

<footer class="site-footer">
  <svg class="footer-bg" width="1200" height="426" viewBox="0 0 1200 426">
    <defs><linearGradient id="footBg" x1="0" y1="0" x2="0" y2="1"><stop offset="0" stop-color="#a01fcc"/><stop offset="1" stop-color="#6a1a86"/></linearGradient></defs>
    <path d="M0 58C120 84 260 104 400 88C600 66 760 8 960 8C1060 8 1140 16 1200 26V426H0Z" fill="url(#footBg)"/>
  </svg>
  <div class="footer-brand"><span class="brand-dot"></span><span class="brand-name">Lumera Beauty</span></div>
</footer>
<div class="f-head" style="left:408px;top:1924px">Treatments</div>
<ul class="f-list treat" style="left:409px;top:1962px"><li>Body treatments</li><li>Face treatments</li><li>Slimming treatments</li></ul>
<div class="f-head" style="left:602px;top:1862px">Quick Links</div>
<ul class="f-list quick" style="left:602px;top:1903px"><li>Home</li><li>About us</li><li>Promotions</li><li>Latest deals</li><li>Treatment</li><li>Products Showcase</li><li>Contact us</li></ul>
<div class="f-head" style="left:828px;top:1860px">Join Us</div>
<div class="join-field" style="top:1906px">Name</div>
<div class="join-field" style="top:1949px">Email</div>
<div class="join-field" style="top:1992px">Phone</div>
<div class="btn-submit">Submit</div>
<div class="footer-rule"></div>
<div class="legal"><span class="sq" aria-hidden="true"></span>Privacy Policy &nbsp;| &nbsp;Terms and Conditions</div>
<div class="copyright">Copyright © 2018 Lumera Beauty HK Ltd. All rights reserved.</div>

</body>
</html>
```